Every Shelf Set Neatly or ESN Organized needs a business card design. ESN Organized is a professi

We need a business card design that is clean, sharp and conveys a sense of organization. I already have a logo.

Target Market(s)

Families (specifically mothers), small business owners, parents, seniors

Industry/Entity Type

Business

Contact Information for Business Card

My website is www.esnorganized-example.com and my Facebook page is http://www.sociallink-example.com/everyshelfsetneatly. The phone number is 418-552-7094 and I want to be listed as Lorna M. Pelham, Owner

Requirements
Must have
• My logo.

```html
<!DOCTYPE html>
<html lang="en">
<head>
<meta charset="utf-8">
<title>ESN Organized – Business Card</title>
<link rel="stylesheet" href="https://fonts.googleapis.com/css2?family=Roboto:wght@400;500;700&family=Roboto+Condensed:wght@400&display=swap">
<style>
  :root {
    --backdrop: #cfcfcf;
    --card-top: #eeeeee;
    --band-grey: #a9a9a9;
    --brand-blue: #2870b6;
    --text-dark: #1d1d1f;
    --white: #ffffff;
    --clip-tone: rgba(255, 255, 255, 0.55);
  }
  * { box-sizing: border-box; margin: 0; padding: 0; }
  html, body {
    width: 1200px; height: 800px; overflow: hidden;
    background: var(--backdrop);
  }
  .canvas {
    position: relative; width: 1200px; height: 800px;
    display: flex; align-items: center; justify-content: center;
  }
  .business-card {
    position: relative; width: 900px; height: 520px;
    border-radius: 38px; overflow: hidden;
    background: var(--brand-blue);
    font-family: "Roboto", Arial, sans-serif;
    box-shadow: 0 18px 40px rgba(0,0,0,0.18);
  }
  .card-header {
    position: absolute; left: 0; top: 0; width: 100%; height: 200px;
    background: var(--card-top);
    display: flex; align-items: flex-end; justify-content: center;
    padding-bottom: 40px;
  }
  .brand-mark { display: flex; align-items: center; gap: 18px; }
  .brand-square { width: 44px; height: 44px; background: var(--brand-blue); }
  .brand-name {
    font-size: 38px; font-weight: 400; letter-spacing: 5px;
    color: var(--text-dark); text-transform: uppercase;
  }
  .tagline-band {
    position: absolute; left: 0; top: 200px; width: 100%; height: 50px;
    background: var(--band-grey);
    display: flex; align-items: center; padding-left: 96px;
  }
  .tagline { font-size: 25px; color: var(--white); }
  .tagline strong { color: var(--brand-blue); font-weight: 700; }
  .paperclip {
    position: absolute; width: 16px; height: 64px;
    border-radius: 8px; background: var(--clip-tone);
  }
  .paperclip--left { left: 52px; top: 228px; }
  .paperclip--right { right: 64px; top: 176px; }
  .owner-block { position: absolute; left: 130px; top: 272px; width: 560px; }
  .rule { height: 2px; background: var(--white); }
  .rule--top { margin-left: 230px; width: 330px; }
  .owner-line {
    display: flex; align-items: baseline; gap: 18px;
    padding: 6px 0 8px 40px; color: var(--white);
  }
  .owner-name { font-size: 36px; font-weight: 400; }
  .owner-title { font-size: 17px; }
  .contact-list {
    list-style: none; position: absolute; left: 160px; top: 350px;
    font-family: "Roboto Condensed", "Arial Narrow", sans-serif;
    color: var(--white); font-size: 24px;
  }
  .contact-item { display: flex; align-items: center; gap: 16px; height: 38px; }
  .contact-icon { width: 26px; height: 26px; flex: none; }
</style>
</head>
<body>
<main class="canvas">
  <section class="business-card" aria-label="ESN Organized business card">
    <header class="card-header">
      <div class="brand-mark">
        <span class="brand-square" aria-hidden="true"></span>
        <span class="brand-name">Every Shelf Set Neatly</span>
      </div>
    </header>

    <div class="tagline-band">
      <p class="tagline">We keep you <strong>organized</strong> in all ways, and always <strong>organized</strong>.</p>
    </div>

    <span class="paperclip paperclip--left" role="img" aria-label="paperclip ornament"></span>
    <span class="paperclip paperclip--right" role="img" aria-label="paperclip ornament"></span>

    <div class="owner-block">
      <div class="rule rule--top"></div>
      <div class="owner-line">
        <span class="owner-name">Lorna M. Pelham</span>
        <span class="owner-title">Owner</span>
      </div>
      <div class="rule"></div>
    </div>

    <ul class="contact-list">
      <li class="contact-item">
        <svg class="contact-icon" viewBox="0 0 28 28" aria-hidden="true" fill="none" stroke="#fff" stroke-width="2">
          <circle cx="14" cy="14" r="12"/>
          <ellipse cx="14" cy="14" rx="5" ry="12"/>
          <line x1="2" y1="14" x2="26" y2="14"/>
        </svg>
        <span>www.esnorganized-example.com</span>
      </li>
      <li class="contact-item">
        <svg class="contact-icon" viewBox="0 0 28 28" aria-hidden="true" fill="none" stroke="#fff" stroke-width="2">
          <circle cx="14" cy="14" r="12"/>
        </svg>
        <span>http://www.sociallink-example.com/everyshelfsetneatly</span>
      </li>
      <li class="contact-item">
        <svg class="contact-icon" viewBox="0 0 28 28" aria-hidden="true" fill="none" stroke="#fff" stroke-width="2">
          <circle cx="14" cy="14" r="12"/>
          <path d="M10 8 l2.5 0 l1 3.5 l-1.8 1.3 c0.8 1.8 2 3 3.6 3.8 l1.3 -1.8 l3.5 1 l0 2.5 c-6 0.5 -10.6 -4 -10.1 -10.3 z" fill="#fff" stroke="none"/>
        </svg>
        <span>418-552-7094</span>
      </li>
    </ul>
  </section>
</main>
</body>
</html>
```